gtw school poster design and change logo name

We already have a logo which only needs to be slightly modified with "school".
We also have two advertising faces, a girl and a boy, which should be on our poster.
Important key data:

bilingual D/E small classes
daycare
private kindergarten
private school from 2024

Poster size: 268,5 x 128 cm
We need logo sizes in different sizes
also for T-shirts.
Attached also a old poster

new clients

0094D4
00A9DD
6FCCEA
C7EBF8
E9F6FB
59FF00
82FF00
B8FF75
E3FFCB
F4FFEA
FFC000
F8CF3A
FAE287
FDF2CF
FEFAEE
F0912C
F2A743
F7CA91
FBE8D2
FDF5EE

```html
<!DOCTYPE html>
<html lang="en">
<head>
<meta charset="utf-8">
<title>gtw school poster</title>
<link rel="stylesheet" href="https://fonts.googleapis.com/css2?family=Fredoka:wght@500;600;700&display=swap">
<style>
  :root {
    --page: #e6e6e6;
    --paper: #ffffff;
    --grid: #a3d2f0;
    --ink: #4a4a4a;
    --orange: #f9a81a;
    --green: #a6ce39;
    --blue: #0fa3dc;
    --pink: #ec2a8c;
    --yellow: #f8cf3a;
    --white: #ffffff;
  }
  * { margin: 0; padding: 0; box-sizing: border-box; }
  html, body { width: 1200px; height: 805px; overflow: hidden; }
  body { background: var(--page); font-family: "Fredoka", sans-serif; position: relative; }

  .poster {
    position: absolute; left: 0; top: 102px;
    width: 1200px; height: 601px; overflow: hidden;
    background-color: var(--paper);
    background-image:
      linear-gradient(to right, var(--grid) 2px, transparent 2px),
      linear-gradient(to bottom, var(--grid) 2px, transparent 2px);
    background-size: 33.6px 33.6px;
    background-position: 8px 8px;
  }
  .poster-art { position: absolute; inset: 0; width: 1200px; height: 601px; }
  .arc-text { font-family: "Fredoka", sans-serif; font-weight: 600; font-size: 40px; fill: var(--ink); }
  .arc-text .year { fill: var(--green); font-size: 44px; }

  .brand {
    position: absolute; left: 385px; top: 130px; width: 400px;
    text-align: center; font-weight: 600; font-size: 54px; line-height: 1;
    color: var(--orange);
  }
  .key-facts {
    position: absolute; left: 290px; top: 352px; width: 600px;
    text-align: center; color: var(--ink); font-weight: 600;
    font-size: 32px; line-height: 45px;
  }
  .contact-pill {
    position: absolute; left: 340px; top: 452px; width: 498px; height: 98px;
    border-radius: 49px; background: var(--orange); color: var(--white);
    text-align: center; padding-top: 12px;
  }
  .contact-phone { font-weight: 600; font-size: 38px; line-height: 44px; display: block; }
  .contact-web { font-weight: 600; font-size: 23px; line-height: 28px; display: block; }
</style>
</head>
<body>
  <section class="poster">
    <svg class="poster-art" viewBox="0 0 1200 601" xmlns="http://www.w3.org/2000/svg">
      <defs>
        <radialGradient id="girl-tones" cx="50%" cy="45%" r="60%">
          <stop offset="0%" stop-color="#f3cdb4"/>
          <stop offset="55%" stop-color="#c99a72"/>
          <stop offset="100%" stop-color="#e3f1fb"/>
        </radialGradient>
        <radialGradient id="boy-tones" cx="50%" cy="55%" r="60%">
          <stop offset="0%" stop-color="#e8b896"/>
          <stop offset="50%" stop-color="#3fb3e6"/>
          <stop offset="100%" stop-color="#ffffff"/>
        </radialGradient>
        <path id="left-arc" d="M83.1 274 A138 138 0 1 1 356.5 262"/>
        <path id="right-arc" d="M835.1 331.5 A135 135 0 1 1 1019.5 380.9"/>
      </defs>

      <!-- kindergarten photo -->
      <circle cx="219" cy="250" r="124" fill="url(#girl-tones)" role="img" aria-label="Photo of a smiling girl holding up paint-covered hands"/>
      <circle class="photo-ring" cx="219" cy="250" r="126.5" fill="none" stroke="var(--orange)" stroke-width="5"/>
      <text class="arc-text"><textPath href="#left-arc" textLength="455" lengthAdjust="spacing">Private Kindergarten</textPath></text>

      <!-- school photo -->
      <circle cx="952" cy="264" r="122" fill="url(#boy-tones)" role="img" aria-label="Photo of a laughing boy in a blue shirt showing paint-covered hands"/>
      <circle class="photo-ring" cx="952" cy="264" r="124.5" fill="none" stroke="var(--green)" stroke-width="5"/>
      <text class="arc-text"><textPath href="#right-arc" textLength="600" lengthAdjust="spacing">Private school from <tspan class="year">2024</tspan></textPath></text>

      <!-- decorative flowers and mascot -->
      <circle cx="403" cy="76" r="18" fill="var(--pink)" role="img" aria-label="Small pink flower decoration"/>
      <circle cx="757" cy="93" r="14" fill="var(--yellow)" role="img" aria-label="Small yellow flower decoration"/>
      <circle cx="226" cy="440" r="22" fill="var(--pink)" role="img" aria-label="Pink flower decoration"/>
      <circle cx="93" cy="507" r="44" fill="var(--blue)" role="img" aria-label="Blue flower decoration"/>
      <circle cx="951" cy="476" r="21" fill="var(--green)" role="img" aria-label="Green flower decoration"/>
      <circle cx="1133" cy="530" r="64" fill="var(--orange)" role="img" aria-label="Large orange flower decoration"/>
      <circle cx="714" cy="418" r="12" fill="var(--pink)" role="img" aria-label="Small pink heart decoration"/>
      <rect x="510" y="302" width="44" height="60" rx="18" fill="#f7c64a" role="img" aria-label="Little singing bird mascot"/>
    </svg>

    <div class="brand">gtw school</div>

    <p class="key-facts">Bilingual D/E small classes<br>Daycare</p>

    <div class="contact-pill">
      <span class="contact-phone">+41 79 000 12 34</span>
      <span class="contact-web">www.gtw-daycare.ch</span>
    </div>
  </section>
</body>
</html>
```